Vantoq Business Card Project showing the logo and a marbo image on the rear

Design a whacky but professional business card, the logo is for the front and the Marbo image is for the rear. Happy to consider other open source Marbo Images if the designer wants to select one from the web. Vantoq is a competitor to OMB.com.au and Pellory.com.au and is based around every property in Australia

Target Market(s)

Business

Contact Information for Business Card

Name, Title, Email, Web, Phone Number

Font styles to use
Other font styles liked:
• avenir

Requirements
Must have
• Image on Back logo on front
Nice to have
• Happy to consider other images on rear, preftably Colin Marbo. Image supplied I own, we can use open source other Marbo Images

```html
<!DOCTYPE html>
<html lang="en">
<head>
<meta charset="utf-8">
<title>Vantoq Business Card</title>
<link rel="stylesheet" href="https://fonts.googleapis.com/css2?family=Lato:wght@400;700&display=swap">
<style>
  :root {
    --page-bg: #e9e7e6;
    --card-light: #ffffff;
    --card-dark: #000000;
    --accent: #ff8a00;
    --ink: #111111;
    --text-light: #ffffff;
  }
  * { box-sizing: border-box; margin: 0; padding: 0; }
  html, body {
    width: 1200px; height: 900px; overflow: hidden;
    background: var(--page-bg);
    font-family: "Lato", sans-serif;
  }
  .business-card {
    position: absolute; left: 100px; top: 140px;
    width: 1000px; height: 620px;
    display: flex;
    box-shadow: 0 10px 30px rgba(0,0,0,0.18);
  }
  .brand-side {
    width: 547px; height: 100%;
    background: var(--card-light);
    display: flex; align-items: center;
    padding-left: 40px; gap: 36px;
  }
  .brand-mark {
    width: 96px; height: 96px; background: var(--accent);
  }
  .brand-name {
    font-weight: 700; font-size: 104px; color: var(--ink);
    letter-spacing: 1px; line-height: 1;
  }
  .accent-bar { width: 9px; height: 100%; background: var(--accent); }
  .details-side {
    position: relative; flex: 1; height: 100%;
    background: var(--card-dark); color: var(--text-light);
  }
  .name-tab {
    position: absolute; left: 0; top: 137px;
    width: 36px; height: 74px;
  }
  .person {
    position: absolute; left: 44px; top: 140px;
  }
  .person-name {
    font-weight: 700; font-size: 37px; color: var(--accent);
    line-height: 1.05; letter-spacing: 0.3px;
  }
  .person-title { font-size: 29px; line-height: 1.25; }
  .contact-list {
    position: absolute; left: 44px; top: 364px; list-style: none;
  }
  .contact-item {
    display: flex; align-items: center; gap: 10px;
    font-size: 28px; height: 38px;
  }
  .contact-icon { width: 30px; height: 30px; flex: none; }
</style>
</head>
<body>
  <div class="business-card">
    <section class="brand-side">
      <div class="brand-mark"></div>
      <div class="brand-name">Vantoq</div>
    </section>
    <div class="accent-bar"></div>
    <section class="details-side">
      <svg class="name-tab" viewBox="0 0 36 74" aria-hidden="true">
        <polygon points="0,0 36,37 0,74" fill="var(--accent)"/>
      </svg>
      <div class="person">
        <div class="person-name">DANIEL HARTLEY</div>
        <div class="person-title">Managing Director</div>
      </div>
      <ul class="contact-list">
        <li class="contact-item">
          <svg class="contact-icon" viewBox="0 0 24 24" aria-hidden="true">
            <path d="M6.6 10.8a15 15 0 0 0 6.6 6.6l2.2-2.2c.3-.3.7-.4 1-.2 1.1.4 2.3.6 3.6.6.6 0 1 .4 1 1V20c0 .6-.4 1-1 1A17 17 0 0 1 3 4c0-.6.4-1 1-1h3.5c.6 0 1 .4 1 1 0 1.3.2 2.5.6 3.6.1.3 0 .7-.2 1z" fill="var(--accent)"/>
            <path d="M14 3a7 7 0 0 1 7 7M14 6.5a3.5 3.5 0 0 1 3.5 3.5" stroke="var(--accent)" stroke-width="1.8" fill="none" stroke-linecap="round"/>
          </svg>
          <span>044-987 654 321</span>
        </li>
        <li class="contact-item">
          <svg class="contact-icon" viewBox="0 0 24 24" aria-hidden="true">
            <rect x="2" y="5" width="20" height="14" fill="var(--accent)"/>
            <path d="M2 5l10 8 10-8M2 19l7-6.5M22 19l-7-6.5" stroke="var(--card-dark)" stroke-width="1.4" fill="none"/>
          </svg>
          <span>hello@vantoqmail.com</span>
        </li>
        <li class="contact-item">
          <svg class="contact-icon" viewBox="0 0 24 24" aria-hidden="true">
            <g stroke="var(--accent)" stroke-width="1.8" fill="none">
              <circle cx="12" cy="12" r="9.5"/>
              <ellipse cx="12" cy="12" rx="4.2" ry="9.5"/>
              <path d="M2.5 12h19M4 7h16M4 17h16"/>
            </g>
          </svg>
          <span>www.vantoqhomes.com</span>
        </li>
      </ul>
    </section>
  </div>
</body>
</html>
```